Exclusive beauty salon needs a price list or services booklet

I need a new very attractive flyer for my beauty salon, containing information on the different services and their prices.
In attachment you can find a pdf of the "old" one, but I'd love to have a beautifully designed new one!
I'd love to have a booklet in format 148 x 148 mm, or in US format, containing 12 or 16 pages, but if you can offer other nice looking designs they are welcome!
The services that need to come in the booklet with their prices can all be found on my website: www.atelierverano.be, starting with
Gelaatsverzorging
Wimperverlenging
Suikerontharing
Wimperlifting
Permanente Make Up
Airbrush Tanning

Target Market(s)

woman from 20 to 89 years old

Industry/Entity Type

Beauty Salon

Font styles to use
Sans Serif

Colors

Designer to choose colors to be used in the design.

Requirements
Must have
• a classy nice look, it must contain details about the services from my beauty salon and their prices, and nice pictures.
• The Names, prices and explanations of the services can easily be found on my website: www.atelierverano.be
Nice to have
• In attachment you can find the "old" price list in pdf, what I need now is a "new booklet" with the new logo and updated services price list.
• I need a very nice and attractive looking booklet, classy chique, Paris chique, looking very expensive.
Should not have
• Not too much colors, not too curly, but still feminine

```html
<!DOCTYPE html>
<html lang="nl">
<head>
<meta charset="utf-8">
<title>Maison Lumeau – gelaatsverzorging</title>
<link href="https://fonts.googleapis.com/css2?family=Source+Sans+3:ital,wght@0,400;0,600;1,400&display=swap" rel="stylesheet">
<style>
  :root {
    --backdrop: #b4d4d5;
    --paper: #f3f2ef;
    --photo-light: #efebec;
    --photo-mid: #e6dcdb;
    --photo-warm: #e9cfc6;
    --aqua-panel: rgba(139, 204, 204, 0.86);
    --ink: #1b1b1b;
    --grey-edge: #989898;
    --grey-mid: #b7b7b7;
    --white: #ffffff;
  }
  * { box-sizing: border-box; margin: 0; padding: 0; }
  html, body {
    width: 1200px;
    height: 700px;
    overflow: hidden;
    background: var(--backdrop);
    font-family: "Source Sans 3", sans-serif;
  }
  .spread {
    position: absolute;
    left: 110px;
    top: 100px;
    width: 980px;
    height: 500px;
    display: flex;
    box-shadow: 0 10px 26px rgba(60, 100, 100, 0.22);
  }
  .page {
    position: relative;
    width: 490px;
    height: 500px;
    background: var(--paper);
  }
  .page--left { box-shadow: inset -14px 0 18px -12px rgba(0,0,0,0.12); }
  .page--right { box-shadow: inset 14px 0 18px -12px rgba(0,0,0,0.12); }

  .cover-photo {
    position: absolute;
    left: 18px;
    top: 14px;
    width: 462px;
    height: 412px;
    background:
      radial-gradient(ellipse 32% 48% at 48% 52%, var(--photo-warm), transparent 70%),
      linear-gradient(90deg, var(--photo-light), var(--photo-mid) 60%, var(--photo-light));
  }
  .quote-panel {
    position: absolute;
    left: 322px;
    top: 96px;
    width: 134px;
    height: 256px;
    background: var(--aqua-panel);
    padding: 22px 10px 0 10px;
    color: var(--white);
    font-size: 19px;
    line-height: 1.52;
  }
  .brand {
    position: absolute;
    left: 0;
    width: 490px;
    top: 442px;
    text-align: center;
    padding-right: 90px;
    color: var(--ink);
    font-weight: 600;
    font-size: 22px;
    letter-spacing: 1px;
  }

  .info-panel {
    position: absolute;
    left: 14px;
    top: 14px;
    width: 456px;
    height: 458px;
    background: linear-gradient(90deg, var(--grey-edge), var(--grey-mid) 50%, var(--grey-edge));
  }
  .info-frame {
    position: absolute;
    left: 100px;
    top: 100px;
    width: 272px;
    height: 216px;
    border: 1px solid var(--white);
    padding: 18px 16px;
    color: var(--white);
    font-size: 11.5px;
    line-height: 1.32;
  }
  .info-intro { font-style: italic; margin-bottom: 10px; }
  .info-lead { margin-bottom: 2px; }
  .benefits { list-style: none; padding-left: 16px; }
  .benefits li { display: flex; align-items: center; gap: 4px; }
  .benefits svg { flex: none; }
</style>
</head>
<body>
  <main class="spread">
    <section class="page page--left">
      <div class="cover-photo" role="img" aria-label="Portretfoto van een glimlachende vrouw met de hand tegen de wang, zachte lichte achtergrond"></div>
      <p class="quote-panel">Een antwoord bieden voor iedere huidconditie, omdat deze uniek is</p>
      <p class="brand">MAISON LUMEAU</p>
    </section>

    <section class="page page--right">
      <div class="info-panel">
        <div class="info-frame">
          <p class="info-intro">Het merk Maison Lumeau heeft een uitgebreid aanbod aan gelaatsverzorgingen, geschikt voor alle “huidproblemen”. Na een persoonlijke huidanalyse wordt een verzorging uitgevoerd die bij u past. Naast de cabineverzorgingen, kan je ook advies krijgen voor de dagelijkse verzorging thuis.</p>
          <p class="info-lead">Gelaatsverzorgingen van Maison Lumeau bieden:</p>
          <ul class="benefits">
            <li><svg width="8" height="7" viewBox="0 0 8 7"><path d="M1 3.5 L3 5.5 L7 1" fill="none" stroke="#fff" stroke-width="1.2"/></svg>een combinatie van plezier en welzijn</li>
            <li><svg width="8" height="7" viewBox="0 0 8 7"><path d="M1 3.5 L3 5.5 L7 1" fill="none" stroke="#fff" stroke-width="1.2"/></svg>een unieke ervaring voor de zintuigen</li>
            <li><svg width="8" height="7" viewBox="0 0 8 7"><path d="M1 3.5 L3 5.5 L7 1" fill="none" stroke="#fff" stroke-width="1.2"/></svg>resultaatgerichte behandelingen</li>
          </ul>
        </div>
      </div>
    </section>
  </main>
</body>
</html>
```